Can you make a cool and versatile Tarn Meridian Powerpoint template?
See www.tarnmeridian-example.co.uk and http://www.examplenet.invalid/company/tarn-meridian-ltd/ (on the right) to see how the logos are currently used - with interchangeably white and black backgrounds.
Target Market(s)
Marketing managers, product managers in HR technology, HR consultants
Industry/Entity Type
It Company
Font styles to use
Sans Serif
Requirements
Must have
- Master slide design, fonts, color theme, etc. Ideally two variations - one with white background (using colorful logo), one with a darker background (using black/white logo).

```html
<!DOCTYPE html>
<html lang="en">
<head>
<meta charset="utf-8">
<title>Tarn Meridian – Presentation Template</title>
<link href="https://fonts.googleapis.com/css2?family=Graduate&family=Open+Sans:wght@400;600&family=Marcellus+SC&display=swap" rel="stylesheet">
<style>
  :root{
    --canvas:#ffffff;
    --slide-dark:#0b0b0b;
    --slide-mid:#2a2a2a;
    --accent:#29abe2;
    --ink:#111111;
    --text-light:#ffffff;
    --text-muted:#555555;
    --pie-green:#2fb36f;
    --pie-teal:#1aa89a;
    --pie-blue:#29abe2;
    --pie-tan:#c49a6c;
    --pie-gray:#6d6e71;
    --pie-lime:#8dc63f;
    --pie-forest:#159447;
  }
  *{box-sizing:border-box;margin:0;padding:0}
  html,body{width:1200px;height:900px;overflow:hidden;background:var(--canvas)}
  body{position:relative;font-family:"Open Sans",Arial,sans-serif}
  .slide{position:absolute;overflow:hidden;
    background:radial-gradient(ellipse at 50% 45%,var(--slide-mid) 0%,#151515 55%,var(--slide-dark) 100%)}
  .slide--title{left:22px;top:278px;width:713px;height:401px}
  .slide--photo{left:752px;top:70px;width:404px;height:226px;border:2px solid #000}
  .slide--bullets{left:754px;top:337px;width:402px;height:224px;border:2px solid #000}
  .slide--graphic{left:754px;top:589px;width:402px;height:224px;border:2px solid #000}

  .title-page__heading{position:absolute;left:0;width:100%;top:28px;text-align:center;
    font-family:"Graduate",serif;font-size:68px;line-height:1;color:var(--accent);letter-spacing:1px;padding-right:20px}
  .title-page__reflection{position:absolute;left:0;width:100%;top:118px;text-align:center;
    font-family:"Graduate",serif;font-size:68px;line-height:1;color:#fff;opacity:.06;transform:scaleY(-1);padding-right:20px}
  .title-page__details{position:absolute;left:0;width:100%;top:101px;text-align:center;
    font-size:15px;color:var(--text-light);padding-right:10px}
  .title-page__details-reflection{position:absolute;left:0;width:100%;top:118px;text-align:center;
    font-size:15px;color:#fff;opacity:.12;transform:scaleY(-1);padding-right:10px}
  .brand-ring{position:absolute;left:293px;top:191px;width:150px;height:150px;border-radius:50%;
    background:#000;border:8px solid var(--accent);display:flex;align-items:center;justify-content:center}
  .brand-name{font-family:"Open Sans",Arial,sans-serif;font-weight:600;color:var(--text-light);white-space:nowrap}
  .brand-ring .brand-name{font-size:17px}
  .title-page__url{position:absolute;left:0;width:100%;top:363px;text-align:center;font-size:15px;color:#3d3d3d;padding-left:14px}
  .corner{position:absolute}
  .corner__num{position:absolute;font-family:"Graduate",serif;color:#fff}

  .photo-frame{position:absolute;left:9px;top:10px;width:223px;height:149px;border:3px solid #fff;
    background:linear-gradient(135deg,#f7c35a 0%,#e08a1e 40%,#8a3d0c 75%,#3a2a2a 100%)}

  .title-band{position:absolute;left:4px;right:4px;height:50px;background:var(--accent)}
  .title-band__title{position:absolute;left:8px;top:4px;font-family:"Graduate",serif;font-size:24px;line-height:1.05;
    color:var(--ink);border-bottom:2px solid var(--ink)}
  .title-band__sub{position:absolute;top:35px;font-size:7px;color:var(--ink);font-weight:600}
  .title-band__contact{position:absolute;right:62px;top:19px;font-size:4.5px;line-height:1.5;color:#0b3d57;text-align:right}
  .title-band__brand{position:absolute;right:4px;top:3px;width:50px;height:44px;background:#000;
    display:flex;align-items:center;justify-content:center}
  .title-band__brand .brand-name{font-size:6.5px}

  .rule{position:absolute;left:8px;top:11px}
  .bullets{position:absolute;left:38px;top:32px;list-style:none}
  .bullets__main{font-family:"Graduate",serif;font-size:15px;color:var(--accent);display:flex;align-items:center;gap:6px}
  .bullets__sub{list-style:none;margin:6px 0 0 30px}
  .bullets__sub li{font-family:"Marcellus SC",serif;font-size:8.5px;color:#ddd;display:flex;align-items:center;gap:4px;height:19.5px}
</style>
</head>
<body>

<section class="slide slide--title">
  <h1 class="title-page__heading">TITLE PAGE</h1>
  <div class="title-page__reflection" aria-hidden="true">TITLE PAGE</div>
  <p class="title-page__details">DETAILS OF PRESENTATION / NAME OF PRESENTOR</p>
  <div class="title-page__details-reflection" aria-hidden="true">DETAILS OF PRESENTATION / NAME OF PRESENTOR</div>
  <div class="brand-ring"><span class="brand-name">Tarn Meridian</span></div>
  <p class="title-page__url">http://tarnmeridian-example.co.uk/</p>
  <svg class="corner" style="left:634px;top:324px" width="79" height="77"><polygon points="79,0 79,77 0,77" fill="var(--accent)"/></svg>
  <span class="corner__num" style="left:667px;top:356px;font-size:25px">01</span>
</section>

<section class="slide slide--photo">
  <div class="photo-frame" role="img" aria-label="Photo: figure holding a dandelion in warm golden sunset light"></div>
  <svg class="corner" style="right:4px;top:3px" width="35" height="35"><polygon points="0,0 35,0 35,35" fill="var(--accent)"/></svg>
  <span class="corner__num" style="right:8px;top:8px;font-size:9px">02</span>
  <div class="title-band" style="top:170px">
    <div class="title-band__title">SLIDE TITLE</div>
    <div class="title-band__sub" style="left:26px">DETAILS OF SLIDE / NAME OF PRESENTOR</div>
    <div class="title-band__contact">WWW.COMPANYSITE.COM<br>INFO@COMPANYSITE.COM</div>
    <div class="title-band__brand"><span class="brand-name">Tarn Meridian</span></div>
  </div>
</section>

<section class="slide slide--bullets">
  <svg class="rule" width="350" height="12"><polygon points="7,1 11,6 7,11 3,6" fill="none" stroke="var(--accent)" stroke-width="1.5"/><line x1="14" y1="6" x2="350" y2="6" stroke="#444" stroke-width="1.5"/></svg>
  <svg class="corner" style="right:4px;top:3px" width="36" height="34"><polygon points="0,0 36,0 36,34" fill="var(--accent)"/></svg>
  <ul class="bullets">
    <li class="bullets__main"><svg width="14" height="14"><polygon points="4,1 10,1 13,7 10,13 4,13 1,7" fill="none" stroke="var(--accent)" stroke-width="2.2"/></svg>MAIN BULLET
    </li>
    <li>
      <ul class="bullets__sub">
        <li><svg width="11" height="11"><polygon points="3,.5 8,.5 10.5,5.5 8,10.5 3,10.5 .5,5.5" fill="var(--accent)" stroke="#fff" stroke-width=".8"/></svg>SUB BULLET FORM</li>
        <li><svg width="11" height="11"><polygon points="3,.5 8,.5 10.5,5.5 8,10.5 3,10.5 .5,5.5" fill="var(--accent)" stroke="#fff" stroke-width=".8"/></svg>SUB BULLET FORM</li>
        <li><svg width="11" height="11"><polygon points="3,.5 8,.5 10.5,5.5 8,10.5 3,10.5 .5,5.5" fill="var(--accent)" stroke="#fff" stroke-width=".8"/></svg>SUB BULLET FORM</li>
      </ul>
    </li>
  </ul>
  <div class="title-band" style="top:170px">
    <div class="title-band__title">SLIDE TITLE</div>
    <div class="title-band__sub" style="left:104px">BULLET FORM</div>
    <div class="title-band__contact">WWW.COMPANYSITE.COM<br>INFO@COMPANYSITE.COM</div>
    <div class="title-band__brand"><span class="brand-name">Tarn Meridian</span></div>
  </div>
</section>

<section class="slide slide--graphic">
  <svg class="rule" width="350" height="12"><polygon points="7,1 11,6 7,11 3,6" fill="none" stroke="var(--accent)" stroke-width="1.5"/><line x1="14" y1="6" x2="345" y2="6" stroke="#444" stroke-width="1.5"/></svg>
  <svg class="corner" style="right:4px;top:3px" width="36" height="34"><polygon points="0,0 36,0 36,34" fill="var(--accent)"/></svg>
  <span class="corner__num" style="right:8px;top:7px;font-size:9px">04</span>
  <svg class="chart" style="position:absolute;left:0;top:0" width="402" height="170" role="img" aria-label="Pyramid chart and pie chart">
    <polygon points="110,64 131,91 88,91" fill="var(--pie-lime)"/>
    <polygon points="86,94 135,94 160,121 58,121" fill="var(--accent)"/>
    <polygon points="56,124 162,124 190,151 28,151" fill="#6d6e71"/>
    <polygon points="28,151 190,151 186,157 32,157" fill="#454547"/>
    <g transform="translate(289,101)">
      <ellipse cx="0" cy="8" rx="58" ry="58" fill="#1b5f7d"/>
      <path d="M0,0 L0,-58 A58,58 0 0 1 45.3,-36.2Z" fill="var(--pie-green)"/>
      <path d="M0,0 L45.3,-36.2 A58,58 0 0 1 56.5,12.9Z" fill="var(--pie-teal)"/>
      <path d="M0,0 L56.5,12.9 A58,58 0 0 1 25.2,52.3Z" fill="var(--pie-blue)"/>
      <path d="M0,0 L25.2,52.3 A58,58 0 0 1 -25.2,52.3Z" fill="var(--pie-tan)"/>
      <path d="M0,0 L-25.2,52.3 A58,58 0 0 1 -56.5,12.9Z" fill="var(--pie-gray)"/>
      <path d="M0,0 L-56.5,12.9 A58,58 0 0 1 -45.3,-36.2Z" fill="var(--pie-lime)"/>
      <path d="M0,0 L-45.3,-36.2 A58,58 0 0 1 0,-58Z" fill="var(--pie-forest)"/>
    </g>
  </svg>
  <div class="title-band" style="top:170px">
    <div class="title-band__title">GRAPHIC SLIDE</div>
    <div class="title-band__sub" style="left:30px">DETAILS OF SLIDE / NAME OF PRESENTOR</div>
    <div class="title-band__contact">WWW.COMPANYSITE.COM<br>INFO@COMPANYSITE.COM</div>
    <div class="title-band__brand"><span class="brand-name">Tarn Meridian</span></div>
  </div>
</section>

</body>
</html>
```